Business Card for Fashion House

We need a business card design for our personalize fashion service for our customers. the business card should reflect reliability, luxury and creativity.
The brand Gravetto is extracted from "Graceful Velvetto"; Gravetto provides fashion designs sprinkled with luxury and style tailored for our elite clients character profile.
Gravetto is created for those who embody class and elegance with a passion for style.
Target Market(s)
Affluent Customers
Industry/Entity Type
Fashion
Contact Information for Business Card
Samira Haddadin
Fashion Designer
Telephone: +971 4 555 0192
Mobile +971 50 555 0147
Emal info@gravetto-example.com
Website www.gravetto-example.com
Social Media Youtube g+ Facebook Instagram Pin /gravetto
Font styles to use
Other font styles liked:
- Audrey provided
Look and feel
Each slider illustrates characteristics of the customer's brand and the style your logo design should communicate.

```html
<!DOCTYPE html>
<html lang="en">
<head>
<meta charset="utf-8">
<title>Gravetto — Business Card</title>
<link rel="stylesheet" href="https://fonts.googleapis.com/css2?family=Marcellus&family=Cormorant+Garamond:ital,wght@1,500&display=swap">
<style>
  :root {
    --stage: #141414;
    --card: #0b0b0b;
    --card-edge: #1c1c1c;
    --ink: #f2f2f2;
    --ink-soft: #cfcfcf;
    --band-light: #e9e9e9;
    --band-dark: #3a3a3a;
  }
  * { box-sizing: border-box; margin: 0; padding: 0; }
  html, body {
    width: 1200px; height: 864px; overflow: hidden;
    background: var(--stage);
  }
  .stage {
    position: relative; width: 1200px; height: 864px;
    display: flex; align-items: center; justify-content: center; gap: 60px;
  }
  .card {
    position: relative; width: 500px; height: 286px;
    background: linear-gradient(160deg, #1a1a1a 0%, var(--card) 45%, #050505 100%);
    border: 1px solid var(--card-edge);
    box-shadow: 0 18px 40px rgba(0,0,0,.6);
    overflow: hidden;
    color: var(--ink);
    font-family: "Marcellus", serif;
  }
  .band-light {
    position: absolute; left: 0; right: 0; bottom: 34px; height: 28px;
    background: var(--band-light);
  }
  .band-dark {
    position: absolute; left: 0; right: 0; bottom: 0; height: 34px;
    background: var(--band-dark);
  }

  /* front */
  .brand {
    position: absolute; left: 40px; top: 28px;
    display: flex; flex-direction: column; align-items: center; gap: 10px;
  }
  .brand-dot {
    width: 30px; height: 30px; border: 2px solid var(--ink); border-radius: 50%;
  }
  .brand-name {
    font-size: 17px; letter-spacing: 7px; color: var(--ink);
  }
  .contacts {
    position: absolute; left: 40px; top: 118px;
    list-style: none; font-size: 12.5px; line-height: 20px; color: var(--ink);
  }
  .contacts li { display: flex; align-items: center; gap: 9px; }
  .contacts svg { width: 12px; height: 12px; flex: none; }
  .holder {
    position: absolute; right: 40px; top: 110px; text-align: right;
  }
  .holder-name { font-size: 15px; letter-spacing: .5px; text-transform: uppercase; }
  .holder-role {
    font-family: "Cormorant Garamond", serif; font-style: italic; font-weight: 500;
    font-size: 13px; color: var(--ink-soft);
  }

  /* back */
  .back .band-light {
    display: flex; align-items: center; padding-left: 70px;
  }
  .back-name {
    font-size: 15px; letter-spacing: 9px; color: #2a2a2a;
  }
</style>
</head>
<body>
<main class="stage">
  <section class="card front" aria-label="Card front">
    <div class="brand">
      <span class="brand-dot"></span>
      <span class="brand-name">GRAVETTO</span>
    </div>
    <ul class="contacts">
      <li>
        <svg viewBox="0 0 12 12"><circle cx="6" cy="6" r="5.3" fill="none" stroke="currentColor"/><path d="M3.5 4.5h5l-.6 3h-3.8z" fill="currentColor"/></svg>
        +971 4 555 0192
      </li>
      <li>
        <svg viewBox="0 0 12 12"><circle cx="6" cy="6" r="5.3" fill="none" stroke="currentColor"/><rect x="4.3" y="3" width="3.4" height="6" rx=".6" fill="none" stroke="currentColor" stroke-width=".9"/></svg>
        +971 50 555 0147
      </li>
      <li>
        <svg viewBox="0 0 12 12"><circle cx="6" cy="6" r="5.3" fill="none" stroke="currentColor"/><rect x="3.3" y="4" width="5.4" height="4" fill="none" stroke="currentColor" stroke-width=".9"/><path d="M3.3 4l2.7 2.2L8.7 4" fill="none" stroke="currentColor" stroke-width=".9"/></svg>
        info@gravetto-example.com
      </li>
      <li>
        <svg viewBox="0 0 12 12"><circle cx="6" cy="6" r="5.3" fill="none" stroke="currentColor"/><circle cx="6" cy="6" r="3" fill="none" stroke="currentColor" stroke-width=".8"/><path d="M3 6h6M6 3v6" stroke="currentColor" stroke-width=".8"/></svg>
        www.gravetto-example.com
      </li>
    </ul>
    <div class="holder">
      <p class="holder-name">Samira Haddadin</p>
      <p class="holder-role">Fashion Designer</p>
    </div>
    <div class="band-light"></div>
    <div class="band-dark"></div>
  </section>

  <section class="card back" aria-label="Card back">
    <div class="band-light"><span class="back-name">GRAVETTO</span></div>
    <div class="band-dark"></div>
  </section>
</main>
</body>
</html>
```